Business card for law firm

Need business card for new law firm. Think confident, authoritative, conservative, but not stuffy or old-fashioned.

Contact Information for Business Card

Content for card - logo (uploaded), plus the following:

Paul Whitcombe (larger font)
Managing Partner (larger font, but not as large as name)
Level 9, 7 Ferris Lane
Sydney NSW 2000
Main Tel 02 9364 2710
Direct Tel 02 8472 3159
Email paul@qvlegal.com.au
www.qvlegal.com.au

Letterhead design should include logo plus:
Level 9, 7 Ferris Lane
Sydney NSW 2000
Tel 02 8472 3159
www.qvlegal.com.au

```html
<!DOCTYPE html>
<html lang="en">
<head>
<meta charset="utf-8">
<title>Quayvale Legal – Business Card</title>
<link rel="stylesheet" href="https://fonts.googleapis.com/css2?family=Open+Sans:wght@400;700&display=swap">
<style>
  :root {
    --navy: #0b1f5c;
    --ink: #111111;
    --text: #222222;
    --paper: #ffffff;
    --backdrop: #d4d5d8;
    --edge: #9a9a9a;
    --rule: #c4c4c4;
  }
  * { margin: 0; padding: 0; box-sizing: border-box; }
  html, body { width: 1200px; height: 1085px; overflow: hidden; }
  body {
    background: var(--backdrop);
    position: relative;
    font-family: "Open Sans", Arial, sans-serif;
    color: var(--text);
  }
  .card {
    position: absolute;
    width: 772px;
    height: 440px;
    background: var(--paper);
    border: 1px solid var(--edge);
    border-radius: 36px;
    overflow: hidden;
  }
  .card--front { left: 360px; top: 74px; }
  .card--back { left: 118px; top: 548px; }

  .brand {
    position: absolute;
    text-align: center;
    font-family: "Open Sans", Arial, sans-serif;
    font-weight: 400;
    color: var(--ink);
  }
  .brand__mark {
    display: block;
    width: 66px;
    height: 66px;
    margin: 0 auto 26px;
    background: var(--navy);
  }
  .brand__name {
    display: block;
    font-size: 34px;
    line-height: 1.2;
  }
  .card--front .brand { left: 85px; width: 330px; top: 112px; }
  .card--back .brand { left: 0; width: 100%; top: 84px; }

  .divider {
    position: absolute;
    left: 430px;
    top: 69px;
    width: 2px;
    height: 265px;
    background: var(--rule);
  }
  .contact {
    position: absolute;
    left: 453px;
    top: 58px;
    font-size: 19px;
    line-height: 1.2;
  }
  .contact__name {
    font-size: 25px;
    font-weight: 700;
    color: var(--navy);
    letter-spacing: 0.3px;
  }
  .contact__role { font-size: 19px; margin-top: 4px; }
  .contact__address { margin-top: 18px; }
  .contact__address p { margin-bottom: 8px; }
  .contact__list { list-style: none; margin-top: 16px; }
  .contact__list li {
    display: flex;
    align-items: center;
    gap: 6px;
    height: 32.5px;
  }
  .contact__list svg { width: 16px; height: 16px; flex: none; }

  .swoosh { position: absolute; left: 0; top: 0; width: 772px; height: 440px; }

  .web {
    position: absolute;
    left: 0;
    width: 100%;
    top: 340px;
    text-align: center;
    font-size: 23px;
    letter-spacing: 3px;
    color: var(--ink);
  }
  .web strong { color: var(--navy); font-weight: 700; }
</style>
</head>
<body>

  <section class="card card--front" aria-label="Card front">
    <svg class="swoosh" viewBox="0 0 772 440" aria-hidden="true">
      <path d="M0 316 Q 250 385 560 410 Q 250 402 0 350 Z" fill="var(--ink)"/>
      <path d="M0 360 Q 270 432 540 418 Q 680 410 772 383 L772 440 L0 440 Z" fill="var(--navy)"/>
    </svg>

    <div class="brand">
      <span class="brand__mark"></span>
      <span class="brand__name">Quayvale Legal</span>
    </div>

    <div class="divider"></div>

    <div class="contact">
      <p class="contact__name">PAUL WHITCOMBE</p>
      <p class="contact__role">MANAGING PARTNER</p>
      <div class="contact__address">
        <p>Level 9, 7 Ferris Lane</p>
        <p>Sydney NSW 2000</p>
      </div>
      <ul class="contact__list">
        <li>
          <svg viewBox="0 0 16 16" aria-hidden="true"><circle cx="8" cy="8" r="7" fill="none" stroke="var(--navy)" stroke-width="1.4"/><path d="M5.5 4.5l1.5 1.5-1 1.2a5 5 0 0 0 2.8 2.8l1.2-1 1.5 1.5-1 1.2C7.8 11.5 4.5 8.2 4.3 5.5z" fill="var(--navy)"/></svg>
          02 9364 2710 (Main)
        </li>
        <li>
          <svg viewBox="0 0 16 16" aria-hidden="true"><circle cx="8" cy="8" r="7" fill="none" stroke="var(--navy)" stroke-width="1.4"/><path d="M5.5 4.5l1.5 1.5-1 1.2a5 5 0 0 0 2.8 2.8l1.2-1 1.5 1.5-1 1.2C7.8 11.5 4.5 8.2 4.3 5.5z" fill="var(--navy)"/></svg>
          02 8472 3159 (Direct)
        </li>
        <li>
          <svg viewBox="0 0 16 16" aria-hidden="true"><path d="M1 6l7-4 7 4v8H1z" fill="var(--navy)"/><path d="M1.5 6.5l6.5 4 6.5-4" fill="none" stroke="#fff" stroke-width="1.3"/></svg>
          paul@qvlegal.com.au
        </li>
        <li>
          <svg viewBox="0 0 16 16" aria-hidden="true"><g fill="none" stroke="var(--navy)" stroke-width="1.3"><circle cx="8" cy="8" r="6.5"/><ellipse cx="8" cy="8" rx="3" ry="6.5"/><path d="M1.5 8h13M2.5 4.8h11M2.5 11.2h11"/></g></svg>
          www.qvlegal.com.au
        </li>
      </ul>
    </div>
  </section>

  <section class="card card--back" aria-label="Card back">
    <div class="brand">
      <span class="brand__mark"></span>
      <span class="brand__name">Quayvale Legal</span>
    </div>
    <p class="web">www.<strong>qvlegal</strong>.com.au</p>
  </section>

</body>
</html>
```